We’re a real estate firm that has landed a big builder in a neighboring state. Our branding needs...

We are a real estate firm who represents various builders along with doing resale here in Oregon. Our firm is growing to represent a big builder in Washington State and we’ll have another 40 brokers on our team. We need rebranding. As in, a new logo ( the house logo we have now looks cartoonish, hate it). We need new cards, something to really stand out. I’ve been thinking of using those NFC cards from ZEP or the ones with the seam color. I likely want two or three designs, a darker (as in a background color of black or grey) , a light one ( again I mean background color) and a credit card style (either plastic w an embossed name/number on front, or metal ). I’m thinking dark background for cc, or silver if it’s metal. That’s my thoughts, but you are the artists, so maybe you have an idea I haven’t considered. Our colors were black and red, but we don’t have to stick to that. Just nothing too busy. Oh, and we are typically representing the local, higher quality builders in our area (just below custom), but not national. Subdivisions are near the Kell Varney, Brisco, and Thornfield Crest sites. We are super excited, but without a lot of time to change the “look” of our brokerage. So I’ll be deciding and moving forward within 24 hours tops. Our name is Real Estate Summit Alliance ( we cant change the name because of timeline and business license) Thank you!

Industry/Entity Type

Real Estate

Contact Information for Business Card

The usual. Name of firm. Name of cardholder. Contact info.

Font styles to use
Serif
Sans Serif

Colors

Designer to choose colors to be used in the design.

Requirements
Must have
• A sleek or simple look. I included photos of cards with stylistic attributes we like. Thank you
Nice to have
• We really like the black backgrounds. With foil or embossed detail. We also like the black on black. Matte black card with raised shiny black detail. But still eye catching.
Should not have
• No ornate or busy looking style. We don’t want anything cluttered.

```html
<!DOCTYPE html>
<html lang="en">
<head>
<meta charset="utf-8">
<title>Real Estate Summit Alliance – Business Card</title>
<link href="https://fonts.googleapis.com/css2?family=Open+Sans:wght@400;600;700&display=swap" rel="stylesheet">
<style>
  :root {
    --navy: #07285c;
    --stripe-grey: #8a8b8e;
    --text-grey: #6f7073;
    --card-light: #f6f6f6;
    --card-light-edge: #e4e5e7;
    --page-bg: #e9e9eb;
    --white: #ffffff;
  }
  * { margin: 0; padding: 0; box-sizing: border-box; }
  html, body {
    width: 1200px;
    height: 900px;
    overflow: hidden;
    background: var(--page-bg);
    font-family: "Open Sans", Arial, sans-serif;
  }
  .business-card {
    position: absolute;
    left: 120px;
    top: 150px;
    width: 960px;
    height: 600px;
    background: linear-gradient(135deg, var(--white) 0%, var(--card-light) 55%, var(--card-light-edge) 100%);
    overflow: hidden;
    box-shadow: 0 10px 30px rgba(0,0,0,0.12);
  }
  .card-shapes {
    position: absolute;
    inset: 0;
  }
  .cardholder {
    position: absolute;
    left: 52px;
    top: 190px;
    color: var(--white);
  }
  .cardholder-name {
    font-size: 32px;
    font-weight: 600;
    letter-spacing: 0.5px;
    line-height: 1.15;
  }
  .cardholder-title {
    font-size: 26px;
    font-weight: 400;
    line-height: 1.2;
  }
  .contact-list {
    position: absolute;
    left: 48px;
    top: 290px;
    list-style: none;
    color: var(--white);
    font-size: 26px;
    line-height: 35px;
  }
  .contact-list li {
    display: flex;
    align-items: center;
    gap: 6px;
  }
  .contact-icon {
    width: 22px;
    height: 22px;
    flex: none;
  }
  .office-address {
    position: absolute;
    left: 52px;
    top: 456px;
    color: var(--white);
    font-size: 26px;
    line-height: 35px;
    font-style: normal;
  }
  .firm-name {
    position: absolute;
    left: 520px;
    top: 200px;
    width: 410px;
    text-align: center;
    color: var(--navy);
    font-size: 52px;
    font-weight: 700;
    line-height: 1.12;
  }
  .firm-dot {
    display: block;
    width: 26px;
    height: 26px;
    margin: 0 auto 22px;
    border-radius: 50%;
    background: var(--stripe-grey);
  }
</style>
</head>
<body>
  <main class="business-card">
    <svg class="card-shapes" width="960" height="600" viewBox="0 0 960 600" aria-hidden="true">
      <polygon class="accent-stripe" points="0,0 332,0 598,490 856,600 0,600" fill="var(--stripe-grey)"/>
      <polygon class="navy-panel" points="0,0 318,0 583,487 842,600 0,600" fill="var(--navy)"/>
    </svg>

    <div class="cardholder">
      <h1 class="cardholder-name">MARCUS ELLERY</h1>
      <p class="cardholder-title">Managing Director</p>
    </div>

    <ul class="contact-list">
      <li>
        <svg class="contact-icon" viewBox="0 0 24 24" aria-hidden="true"><path fill="#fff" d="M3 9c0-3 4-5 9-5s9 2 9 5v2h-5V9c-1-.6-2.4-1-4-1s-3 .4-4 1v2H3zM6 12h12l2 7H4z"/></svg>
        <span>503-555 0142</span>
      </li>
      <li>
        <svg class="contact-icon" viewBox="0 0 24 24" aria-hidden="true"><rect x="7" y="2" width="10" height="20" rx="2" fill="none" stroke="#fff" stroke-width="2"/><circle cx="12" cy="18" r="1.2" fill="#fff"/></svg>
        <span>503-555 0142</span>
      </li>
      <li>
        <svg class="contact-icon" viewBox="0 0 24 24" aria-hidden="true"><rect x="3" y="6" width="18" height="12" fill="#fff"/><path d="M3 6l9 7 9-7" fill="none" stroke="var(--navy)" stroke-width="1.6"/></svg>
        <span>info@summitalliance.com</span>
      </li>
      <li>
        <svg class="contact-icon" viewBox="0 0 24 24" aria-hidden="true"><circle cx="12" cy="12" r="9" fill="#fff"/><path d="M8 8c2 0 3 1 2 3s-3 1-3 4M15 6c-1 2 1 3 2 3M14 18c0-2 1-3 3-3" fill="none" stroke="var(--navy)" stroke-width="1.6"/></svg>
        <span>www.summitalliance.com</span>
      </li>
    </ul>

    <address class="office-address">
      4410 Ridgeview Lane<br>
      Portland, OR 97201
    </address>

    <div class="firm-name">
      <span class="firm-dot" aria-hidden="true"></span>
      Real Estate<br>Summit Alliance
    </div>
  </main>
</body>
</html>
```